OrvanoGoodsHub.com -Ecommerce Website for Luxury Products

This will be an ecommerce site. A website portal that will allow both consumers to enter one way and see specific purchase options and businesses to enter via a different link that allows B2B to see their specific options once logged into. B2C can purchase both as a guest/or after account is setup. B2B must be approved to set up account. This is front end website project. Back-end integration is separate. Will be hosted on Servantia with a domain registration held at Pexadrinet. Additional website concept/idea/synergy can be found from sister site-KRWZHospitality.com

```html
<!DOCTYPE html>
<html lang="en">
<head>
<meta charset="utf-8">
<title>OrvanoGoods — Site Screens</title>
<link rel="stylesheet" href="https://fonts.googleapis.com/css2?family=Inter:wght@400;500;600&family=Playfair+Display:ital,wght@0,400;0,500;1,400&display=swap">
<style>
:root{
  --canvas:#8a8a8a;
  --black:#0a0a0a;
  --ink:#1b1b1b;
  --muted:#6b6b6b;
  --line:#e4e4e4;
  --soft:#f5f5f6;
  --orange:#d96b0c;
  --orange-deep:#a8500a;
  --navy-top:#1d2230;
  --navy-bottom:#0b0d12;
  --cream:#fdf8e8;
  --white:#ffffff;
}
*{box-sizing:border-box;margin:0;padding:0}
html,body{width:1200px;height:1200px;overflow:hidden;background:var(--canvas)}
.board{position:relative;width:1932px;height:1932px;transform:scale(.62112);transform-origin:0 0}
.page{position:absolute;background:var(--white);overflow:hidden;font-family:'Inter',sans-serif;color:var(--ink);box-shadow:0 2px 6px rgba(0,0,0,.15)}
.a{position:absolute}
.serif{font-family:'Playfair Display',serif;font-weight:400}
.center{left:0;right:0;text-align:center}
.muted{color:var(--muted)}
.or{color:var(--orange)}
.w{color:var(--white)}

/* navigation */
.nav{position:absolute;left:0;top:0;width:100%;height:24px;background:var(--black);font-size:4.2px;color:var(--white)}
.brand{position:absolute;left:20px;top:8px;display:flex;align-items:center;gap:2px;font-family:'Playfair Display',serif;font-size:5.2px;letter-spacing:.3px;color:var(--white)}
.brand i{display:block;width:5px;height:5px;border:0.6px solid var(--white)}
.links{position:absolute;left:110px;top:9px;display:flex;gap:9px}
.links .on{color:var(--orange)}
.nav-btn{position:absolute;left:276px;top:6px;width:46px;height:11px;background:var(--orange);font-size:4.2px;line-height:11px;text-align:center}
.nav-ic{position:absolute;left:355px;top:8px;display:flex;gap:4px}

/* footer */
.foot{position:absolute;left:0;bottom:0;width:100%;height:94px;background:var(--black);color:#bdbdbd;font-size:3.6px;line-height:6px}
.foot .brand{top:14px}
.foot .tag{position:absolute;left:20px;top:26px;width:70px}
.foot .col{position:absolute;top:14px}
.foot .col b{display:block;color:var(--white);font-weight:500;margin-bottom:2px}
.foot .rule{position:absolute;left:20px;right:20px;top:66px;border-top:0.5px solid #2a2a2a}
.foot .copy{position:absolute;left:0;right:0;top:73px;text-align:center;font-size:3.4px}

/* shared blocks */
.ph{position:absolute;background:linear-gradient(135deg,#6a4424,#2b1a10)}
.dark-head{position:absolute;left:0;width:100%;background:linear-gradient(180deg,var(--navy-top),var(--navy-bottom))}
.band-orange{position:absolute;left:0;width:100%;background:linear-gradient(180deg,var(--orange),var(--orange-deep))}
.btn{position:absolute;height:17px;font-size:4px;line-height:17px;text-align:center}
.btn.fill{background:var(--orange);color:var(--white)}
.btn.ghost{border:0.8px solid var(--white);color:var(--white)}
.btn.white{background:var(--white);color:var(--orange)}
.card{position:absolute;background:var(--white);box-shadow:0 1px 4px rgba(0,0,0,.12)}
.tag-badge{position:absolute;background:var(--orange);color:var(--white);font-size:3.4px;padding:1.5px 3px}
.h-sec{position:absolute;font-family:'Playfair Display',serif;font-size:11px}
.sub{position:absolute;font-size:4px;color:var(--muted)}
.small{font-size:3.6px;line-height:5.5px;color:var(--muted)}

/* product grid */
.prod .ph{background:linear-gradient(160deg,#f1f1f1,#cfcfcf)}
.prod .name{position:absolute;font-family:'Playfair Display',serif;font-size:4.4px}
.prod .desc{position:absolute;font-size:3.4px;line-height:4.8px;color:var(--muted);width:105px}
.prod .price{position:absolute;font-size:4.2px;color:var(--orange)}

/* partner cards */
.venue .ph{background:linear-gradient(135deg,#5b3b22,#1f140c)}
.venue .title{position:absolute;font-family:'Playfair Display',serif;font-size:5.2px}
.venue .loc{position:absolute;font-size:3.6px;color:var(--muted)}
.venue .txt{position:absolute;font-size:3.6px;line-height:5.4px;color:var(--muted)}
.venue .lnk{position:absolute;font-size:3.6px;color:var(--orange)}

/* form */
.field-label{position:absolute;font-size:3.6px}
.field{position:absolute;height:11px;border:0.6px solid var(--line);font-size:3.4px;color:#9a9a9a;padding:3px 4px}
.bullet{display:flex;gap:3px;align-items:flex-start}
.dot{width:5px;height:5px;border-radius:50%;background:var(--orange);flex:none;margin-top:1px}
</style>
</head>
<body>
<div class="board">

<!-- ================= HOME ================= -->
<section class="page" style="left:116px;top:51px;width:390px;height:814px">
  <header class="nav">
    <div class="brand"><i></i>ORVANOGOODS</div>
    <div class="links"><span class="on">Home</span><span>About</span><span>Retail Collections</span><span>Partner Showcase</span><span>Contact</span></div>
    <div class="nav-btn">Wholesale Portal</div>
    <div class="nav-ic"><svg width="5" height="5" viewBox="0 0 10 10"><circle cx="5" cy="3" r="2.2" fill="none" stroke="#fff"/><path d="M1 10a4 4 0 0 1 8 0" fill="none" stroke="#fff"/></svg><svg width="5" height="5" viewBox="0 0 10 10"><path d="M0 1h2l1.5 6h5L10 3H3" fill="none" stroke="#fff"/></svg></div>
  </header>
  <div class="ph" role="img" aria-label="Dim study desk with crystal decanter, leather and pen" style="left:0;top:24px;width:390px;height:172px;background:linear-gradient(100deg,#1a100a 0%,#3d2414 45%,#6b4326 80%,#3b2415 100%)"></div>
  <div class="a or" style="left:20px;top:63px;font-size:4.4px;letter-spacing:.4px">♛ LUXURY REDEFINED</div>
  <div class="a serif w" style="left:20px;top:75px;font-size:21px;line-height:21px">Purveyors of Luxury<br>Lifestyle Accoutrements</div>
  <div class="a w" style="left:20px;top:125px;font-size:5px">Curated for connoisseurs. Crafted for lounges.</div>
  <div class="btn fill" style="left:20px;top:141px;width:68px">Explore Collections →</div>
  <div class="btn ghost" style="left:93px;top:141px;width:64px">Wholesale Portal</div>

  <div class="card" style="left:20px;top:219px;width:171px;height:81px">
    <svg class="a" style="left:10px;top:11px" width="12" height="12" viewBox="0 0 12 12"><path d="M6 1v4M4 3h4M2 7l3 3M9 7l-2 4" stroke="#d96b0c" fill="none"/></svg>
    <div class="a serif" style="left:10px;top:29px;font-size:8px">For Connoisseurs</div>
    <div class="a small" style="left:10px;top:43px;width:150px">Discover exclusive, limited-edition luxury items. From the humidor to the wardrobe—indulge in the extraordinary.</div>
    <div class="a or" style="left:10px;top:64px;font-size:3.8px">Shop Retail Collections →</div>
  </div>
  <div class="card" style="left:199px;top:219px;width:171px;height:81px;background:var(--black)">
    <svg class="a" style="left:10px;top:11px" width="12" height="12" viewBox="0 0 12 12"><circle cx="4" cy="4" r="2" fill="none" stroke="#d96b0c"/><circle cx="8.5" cy="4.5" r="1.6" fill="none" stroke="#d96b0c"/><path d="M0.5 11a3.5 3.5 0 0 1 7 0M7 10.5a3 3 0 0 1 4.5-2" fill="none" stroke="#d96b0c"/></svg>
    <div class="a serif w" style="left:10px;top:29px;font-size:8px">For Businesses</div>
    <div class="a small" style="left:10px;top:43px;width:150px;color:#bbb">Elevate your lounge. Impress your clientele. Partner with OrvanoGoods to offer unparalleled luxury to your guests.</div>
    <div class="a or" style="left:10px;top:64px;font-size:3.8px">Access Wholesale Portal →</div>
  </div>

  <div class="h-sec center" style="top:346px">Featured Collections</div>
  <div class="sub center" style="top:363px">Curating limited edition luxury items is fun... but one of a kind is LUXE.</div>
  <div class="ph" role="img" aria-label="Cigar resting on ashtray beside a lighter" style="left:20px;top:383px;width:110px;height:92px;background:linear-gradient(160deg,#5e3c22,#1c120b)"></div>
  <div class="ph" role="img" aria-label="Perfume and oil bottles on a dark shelf" style="left:140px;top:383px;width:110px;height:92px;background:linear-gradient(160deg,#8a7a62,#2a241d)"></div>
  <div class="ph" role="img" aria-label="Watch, cufflinks and tie accessories" style="left:260px;top:383px;width:110px;height:92px;background:linear-gradient(160deg,#56606e,#1e232b)"></div>
  <div class="a serif w" style="left:27px;top:452px;font-size:6px">Cigar Accessories</div><div class="a w" style="left:27px;top:462px;font-size:3.2px">Humidors, cutters, and more</div>
  <div class="a serif w" style="left:147px;top:452px;font-size:6px">Oils &amp; Fragrances</div><div class="a w" style="left:147px;top:462px;font-size:3.2px">Signature scents for the refined</div>
  <div class="a serif w" style="left:267px;top:452px;font-size:6px">Attire &amp; Accessories</div><div class="a w" style="left:267px;top:462px;font-size:3.2px">Refined fashion for discerning tastes</div>

  <div class="a" style="left:0;top:498px;width:390px;height:122px;background:var(--black)"></div>
  <svg class="a" style="left:187px;top:524px" width="16" height="13" viewBox="0 0 16 13"><path d="M1 3l3.5 4L8 1l3.5 6L15 3l-1.5 8h-11z" fill="none" stroke="#d96b0c" stroke-width="1.2"/></svg>
  <div class="a serif w center" style="top:548px;font-size:9.5px">The OrvanoGoods Philosophy</div>
  <div class="a w center" style="top:565px;font-size:4.6px;line-height:7px">We believe luxury is not just about possession—it's about experience, craftsmanship,<br>and the confidence that comes from owning something truly exceptional.</div>
  <div class="a or center" style="top:591px;font-size:4px">Discover Our Story →</div>

  <div class="band-orange" style="top:620px;height:100px"></div>
  <div class="a serif w center" style="top:644px;font-size:9.5px">Ready to Experience True Luxury?</div>
  <div class="a w center" style="top:663px;font-size:4.6px">Join our exclusive community of connoisseurs and business partners.</div>
  <div class="btn white" style="left:133px;top:677px;width:59px">Browse Collections</div>
  <div class="btn ghost" style="left:198px;top:677px;width:59px">Contact Concierge</div>

  <footer class="foot">
    <div class="brand"><i></i>ORVANOGOODS</div>
    <div class="tag">A Division of KRWZ Hospitality<br>"Purveyors of Luxury Lifestyle Accoutrements."</div>
    <div class="col" style="left:110px"><b>Shop</b>All Collections<br>Cigar Accessories<br>Oils &amp; Fragrances<br>Attire &amp; Accessories</div>
    <div class="col" style="left:200px"><b>Business</b>Wholesale Portal<br>Partner Showcase<br>B2B Inquiries</div>
    <div class="col" style="left:290px"><b>Support</b>Contact &amp; Concierge<br>About Us<br>KRWZ Hospitality</div>
    <div class="rule"></div>
    <div class="copy">© 2026 OrvanoGoods. All rights reserved.</div>
  </footer>
</section>

<!-- ================= RETAIL COLLECTIONS ================= -->
<section class="page prod" style="left:557px;top:51px;width:390px;height:709px">
  <header class="nav">
    <div class="brand"><i></i>ORVANOGOODS</div>
    <div class="links"><span>Home</span><span>About</span><span class="on">Retail Collections</span><span>Partner Showcase</span><span>Contact</span></div>
    <div class="nav-btn">Wholesale Portal</div>
    <div class="nav-ic"><svg width="5" height="5" viewBox="0 0 10 10"><circle cx="5" cy="3" r="2.2" fill="none" stroke="#fff"/><path d="M1 10a4 4 0 0 1 8 0" fill="none" stroke="#fff"/></svg><svg width="5" height="5" viewBox="0 0 10 10"><path d="M0 1h2l1.5 6h5L10 3H3" fill="none" stroke="#fff"/></svg></div>
  </header>
  <div class="dark-head" style="top:24px;height:63px"></div>
  <div class="a serif w" style="left:20px;top:41px;font-size:13px">Retail Collections</div>
  <div class="a" style="left:20px;top:60px;font-size:5px;color:#c9c9c9">Curated luxury for the discerning individual</div>
  <div class="a" style="left:0;top:87px;width:390px;height:20px;border-bottom:0.6px solid var(--line)"></div>
  <div class="a" style="left:20px;top:92px;display:flex;gap:4px;font-size:3.6px">
    <span style="background:var(--black);color:#fff;padding:2px 4px">All Collections</span>
    <span style="border:0.5px solid var(--line);padding:2px 4px">Cigar Accessories</span>
    <span style="border:0.5px solid var(--line);padding:2px 4px">Oils &amp; Fragrances</span>
    <span style="border:0.5px solid var(--line);padding:2px 4px">Attire &amp; Accessories</span>
  </div>
  <div class="a" style="left:298px;top:93px;width:48px;height:8px;border:0.5px solid var(--line)"></div>
  <div class="a" style="left:350px;top:93px;width:8px;height:8px;background:#ddd"></div>
  <div class="a" style="left:360px;top:93px;width:8px;height:8px;border:0.5px solid var(--line)"></div>
  <div class="a muted" style="left:20px;top:122px;font-size:3.8px">Showing 9 items</div>

  <div class="ph" role="img" aria-label="Cedar humidor with hygrometer" style="left:20px;top:138px;width:110px;height:110px"></div>
  <div class="ph" role="img" aria-label="Steel cigar cutter" style="left:140px;top:138px;width:110px;height:110px"></div>
  <div class="ph" role="img" aria-label="Oud fragrance bottle" style="left:260px;top:138px;width:110px;height:110px"></div>
  <div class="tag-badge" style="left:24px;top:142px">Limited Edition</div>
  <div class="tag-badge" style="left:264px;top:142px">Exclusive</div>
  <div class="name" style="left:20px;top:254px">Premium Cedar Humidor</div><div class="desc" style="left:20px;top:262px">Hand-crafted Spanish cedar humidor with precision hygrometer</div><div class="price" style="left:20px;top:276px">$899</div>
  <div class="name" style="left:140px;top:254px">Stainless Steel Cigar Cutter</div><div class="desc" style="left:140px;top:262px">Precision-engineered guillotine cutter with lifetime warranty</div><div class="price" style="left:140px;top:276px">$149</div>
  <div class="name" style="left:260px;top:254px">Oud Noir Fragrance</div><div class="desc" style="left:260px;top:262px">Luxurious oud and amber blend, 100ml</div><div class="price" style="left:260px;top:270px">$295</div>

  <div class="ph" role="img" aria-label="Beard oil dropper bottle" style="left:20px;top:302px;width:110px;height:110px"></div>
  <div class="ph" role="img" aria-label="Tan leather briefcase" style="left:140px;top:302px;width:110px;height:110px"></div>
  <div class="ph" role="img" aria-label="Folded silk pocket squares" style="left:260px;top:302px;width:110px;height:110px"></div>
  <div class="tag-badge" style="left:144px;top:306px">One of a Kind</div>
  <div class="tag-badge" style="left:264px;top:306px">Limited Edition</div>
  <div class="name" style="left:20px;top:418px">Sandalwood Beard Oil</div><div class="desc" style="left:20px;top:426px">Premium grooming oil with natural ingredients</div><div class="price" style="left:20px;top:434px">$68</div>
  <div class="name" style="left:140px;top:418px">Italian Leather Briefcase</div><div class="desc" style="left:140px;top:426px">Full-grain Tuscan leather with brass hardware</div><div class="price" style="left:140px;top:434px">$1,200</div>
  <div class="name" style="left:260px;top:418px">Silk Pocket Square Set</div><div class="desc" style="left:260px;top:426px">Hand-rolled silk, set of 5 unique patterns</div><div class="price" style="left:260px;top:434px">$180</div>

  <div class="ph" role="img" aria-label="Crystal decanter with glasses" style="left:20px;top:459px;width:110px;height:111px"></div>
  <div class="ph" role="img" aria-label="Lacquered watch roll box" style="left:140px;top:459px;width:110px;height:111px"></div>
  <div class="ph" role="img" aria-label="Reed diffuser bottle" style="left:260px;top:459px;width:110px;height:111px"></div>
  <div class="tag-badge" style="left:144px;top:463px">Exclusive</div>
  <div class="name" style="left:20px;top:576px">Crystal Whiskey Decanter</div><div class="desc" style="left:20px;top:584px">Lead-free crystal with 4 matching glasses</div><div class="price" style="left:20px;top:592px">$425</div>
  <div class="name" style="left:140px;top:576px">Vintage Cognac Leather Watch Roll</div><div class="desc" style="left:140px;top:584px">Holds up to 6 timepieces, handmade in Italy</div><div class="price" style="left:140px;top:592px">$320</div>
  <div class="name" style="left:260px;top:576px">Bergamot &amp; Vetiver Room Spray</div><div class="desc" style="left:260px;top:584px">Luxury room fragrance, 250ml</div><div class="price" style="left:260px;top:592px">$95</div>

  <footer class="foot">
    <div class="brand"><i></i>ORVANOGOODS</div>
    <div class="tag">A Division of KRWZ Hospitality<br>"Purveyors of Luxury Lifestyle Accoutrements."</div>
    <div class="col" style="left:110px"><b>Shop</b>All Collections<br>Cigar Accessories<br>Oils &amp; Fragrances<br>Attire &amp; Accessories</div>
    <div class="col" style="left:200px"><b>Business</b>Wholesale Portal<br>Partner Showcase<br>B2B Inquiries</div>
    <div class="col" style="left:290px"><b>Support</b>Contact &amp; Concierge<br>About Us<br>KRWZ Hospitality</div>
    <div class="rule"></div>
    <div class="copy">© 2026 OrvanoGoods. All rights reserved.</div>
  </footer>
</section>

<!-- ================= PARTNER SHOWCASE ================= -->
<section class="page venue" style="left:998px;top:51px;width:390px;height:1012px">
  <header class="nav">
    <div class="brand"><i></i>ORVANOGOODS</div>
    <div class="links"><span>Home</span><span>About</span><span>Retail Collections</span><span class="on">Partner Showcase</span><span>Contact</span></div>
    <div class="nav-btn">Wholesale Portal</div>
    <div class="nav-ic"><svg width="5" height="5" viewBox="0 0 10 10"><circle cx="5" cy="3" r="2.2" fill="none" stroke="#fff"/><path d="M1 10a4 4 0 0 1 8 0" fill="none" stroke="#fff"/></svg><svg width="5" height="5" viewBox="0 0 10 10"><path d="M0 1h2l1.5 6h5L10 3H3" fill="none" stroke="#fff"/></svg></div>
  </header>
  <div class="dark-head" style="top:24px;height:71px"></div>
  <div class="a serif w center" style="top:42px;font-size:13px">Partner Showcase</div>
  <div class="a center" style="top:61px;font-size:4.6px;line-height:7px;color:#c9c9c9">Discover the distinguished lounges, clubs, and venues that<br>trust OrvanoGoods to elevate their guest experience.</div>

  <div class="a" style="left:10px;top:117px;width:370px;height:212px;background:var(--soft)"></div>
  <div class="a" style="left:172px;top:120px;width:46px;height:7px;background:#fbe7d3;border-radius:4px;font-size:3.2px;color:var(--orange);text-align:center;line-height:7px">● Featured Partners</div>
  <div class="h-sec center" style="top:133px">Spotlight Venues</div>
  <div class="sub center" style="top:150px">Our premier partners setting the standard for luxury experiences.</div>
  <div class="card" style="left:20px;top:170px;width:171px;height:146px"></div>
  <div class="card" style="left:200px;top:170px;width:171px;height:146px"></div>
  <div class="ph" role="img" aria-label="Chandelier-lit lounge interior" style="left:20px;top:170px;width:171px;height:74px"></div>
  <div class="ph" role="img" aria-label="Lit storefront of a bourbon bar at night" style="left:200px;top:170px;width:171px;height:74px;background:linear-gradient(135deg,#3a3f4a,#7a5a35)"></div>
  <div class="tag-badge" style="left:161px;top:175px;border-radius:3px">● Featured</div>
  <div class="tag-badge" style="left:341px;top:175px;border-radius:3px">● Featured</div>
  <div class="title" style="left:29px;top:253px">The Marlowe Lounge</div><div class="loc" style="left:29px;top:265px">⌖ Miami, FL</div>
  <div class="txt" style="left:29px;top:277px;width:150px">A premier destination for cigar enthusiasts, featuring an extensive selection of rare cigars and OrvanoGoods accessories.</div>
  <div class="lnk" style="left:29px;top:299px">Visit Website ↗</div>
  <div class="title" style="left:209px;top:253px">Cask &amp; Ember</div><div class="loc" style="left:209px;top:265px">⌖ Nashville, TN</div>
  <div class="txt" style="left:209px;top:277px;width:150px">Where Southern hospitality meets luxury. Our members enjoy the finest spirits and cigars in an elegant atmosphere.</div>
  <div class="lnk" style="left:209px;top:299px">Visit Website ↗</div>

  <div class="h-sec center" style="top:361px">Our Partners</div>
  <div class="sub center" style="top:378px">A curated selection of establishments that share our commitment to excellence.</div>
  <div class="card" style="left:20px;top:398px;width:110px;height:122px"></div>
  <div class="card" style="left:140px;top:398px;width:110px;height:122px"></div>
  <div class="card" style="left:260px;top:398px;width:110px;height:122px"></div>
  <div class="card" style="left:20px;top:527px;width:110px;height:119px"></div>
  <div class="ph" role="img" aria-label="Wood-panelled club room" style="left:20px;top:398px;width:110px;height:56px"></div>
  <div class="ph" role="img" aria-label="Dark green velvet lounge" style="left:140px;top:398px;width:110px;height:56px;background:linear-gradient(135deg,#25352c,#0e1511)"></div>
  <div class="ph" role="img" aria-label="Wine cellar racks" style="left:260px;top:398px;width:110px;height:56px;background:linear-gradient(135deg,#7a4a25,#2a160b)"></div>
  <div class="ph" role="img" aria-label="Whiskey glass and cigar on a bar" style="left:20px;top:527px;width:110px;height:56px;background:linear-gradient(135deg,#4a2c16,#0d0806)"></div>
  <div class="title" style="left:27px;top:461px">Halvorsen Club</div><div class="loc" style="left:27px;top:471px">⌖ New York, NY</div>
  <div class="txt" style="left:27px;top:480px;width:96px">An exclusive members-only club offering OrvanoGoods curated collections in the heart of Manhattan.</div><div class="lnk" style="left:27px;top:505px">Learn More ↗</div>
  <div class="title" style="left:147px;top:461px">The Sable Room</div><div class="loc" style="left:147px;top:471px">⌖ Las Vegas, NV</div>
  <div class="txt" style="left:147px;top:480px;width:96px">Las Vegas' most sophisticated cigar lounge, featuring OrvanoGoods exclusive product line.</div><div class="lnk" style="left:147px;top:498px">Learn More ↗</div>
  <div class="title" style="left:267px;top:461px">Bayline Social</div><div class="loc" style="left:267px;top:471px">⌖ San Francisco, CA</div>
  <div class="txt" style="left:267px;top:480px;width:96px">A refined gathering space for connoisseurs, stocked with premium cigars and luxury accessories.</div><div class="lnk" style="left:267px;top:505px">Learn More ↗</div>
  <div class="title" style="left:27px;top:590px">Oak &amp; Cinder</div><div class="loc" style="left:27px;top:600px">⌖ Chicago, IL</div>
  <div class="txt" style="left:27px;top:609px;width:96px">Chicago's finest cigar lounge combines classic elegance with modern luxury, powered by OrvanoGoods.</div><div class="lnk" style="left:27px;top:634px">Learn More ↗</div>

  <div class="band-orange" style="top:670px;height:108px"></div>
  <div class="a serif w center" style="top:694px;font-size:9.5px">Become a OrvanoGoods Partner</div>
  <div class="a w center" style="top:712px;font-size:4.6px;line-height:7px">Join our exclusive network of premium venues and offer your guests the finest luxury<br>lifestyle accoutrements.</div>
  <div class="btn white" style="left:122px;top:735px;width:82px">Apply for Wholesale Account</div>
  <div class="btn ghost" style="left:209px;top:735px;width:59px">Contact Our Team</div>

  <div class="a" style="left:10px;top:800px;width:370px;height:96px;background:var(--soft)"></div>
  <div class="h-sec center" style="top:800px">Find a Partner Near You</div>
  <div class="sub center" style="top:817px">Experience OrvanoGoods products at these fine establishments.</div>
  <div class="card" style="left:20px;top:838px;width:350px;height:57px"></div>
  <svg class="a" style="left:189px;top:851px" width="12" height="14" viewBox="0 0 12 14"><path d="M6 13s5-5 5-8a5 5 0 0 0-10 0c0 3 5 8 5 8z" fill="none" stroke="#d96b0c" stroke-width="1.1"/><circle cx="6" cy="5" r="1.8" fill="none" stroke="#d96b0c"/></svg>
  <div class="a muted center" style="top:875px;font-size:4px">Interactive map coming soon. Contact us to find the nearest OrvanoGoods partner location.</div>

  <footer class="foot">
    <div class="brand"><i></i>ORVANOGOODS</div>
    <div class="tag">A Division of KRWZ Hospitality<br>"Purveyors of Luxury Lifestyle Accoutrements."</div>
    <div class="col" style="left:110px"><b>Shop</b>All Collections<br>Cigar Accessories<br>Oils &amp; Fragrances<br>Attire &amp; Accessories</div>
    <div class="col" style="left:200px"><b>Business</b>Wholesale Portal<br>Partner Showcase<br>B2B Inquiries</div>
    <div class="col" style="left:290px"><b>Support</b>Contact &amp; Concierge<br>About Us<br>KRWZ Hospitality</div>
    <div class="rule"></div>
    <div class="copy">© 2026 OrvanoGoods. All rights reserved.</div>
  </footer>
</section>

<!-- ================= CONTACT ================= -->
<section class="page" style="left:1439px;top:51px;width:390px;height:587px">
  <header class="nav">
    <div class="brand"><i></i>ORVANOGOODS</div>
    <div class="links"><span>Home</span><span>About</span><span>Retail Collections</span><span>Partner Showcase</span><span class="on">Contact</span></div>
    <div class="nav-btn">Wholesale Portal</div>
    <div class="nav-ic"><svg width="5" height="5" viewBox="0 0 10 10"><circle cx="5" cy="3" r="2.2" fill="none" stroke="#fff"/><path d="M1 10a4 4 0 0 1 8 0" fill="none" stroke="#fff"/></svg><svg width="5" height="5" viewBox="0 0 10 10"><path d="M0 1h2l1.5 6h5L10 3H3" fill="none" stroke="#fff"/></svg></div>
  </header>
  <div class="dark-head" style="top:24px;height:96px"></div>
  <svg class="a" style="left:187px;top:44px" width="17" height="15" viewBox="0 0 17 15"><path d="M1 1h15v10H5l-4 3z" fill="none" stroke="#d96b0c" stroke-width="1.2"/></svg>
  <div class="a serif w center" style="top:67px;font-size:13px">Contact &amp; Concierge</div>
  <div class="a center" style="top:86px;font-size:4.6px;line-height:7px;color:#c9c9c9">Our dedicated team is here to assist with your inquiries,<br>custom orders, and partnership opportunities.</div>

  <div class="a serif" style="left:20px;top:135px;font-size:8px">Get in Touch</div>
  <div class="a" style="left:20px;top:155px;width:9px;height:9px;background:#fbe7d3;border-radius:2px"></div>
  <div class="a" style="left:38px;top:154px;font-size:3.6px;line-height:5.2px">Email<br>info@orvanogoods.com<br><span class="muted">Response within 24 hours</span></div>
  <div class="a" style="left:20px;top:184px;width:9px;height:9px;background:#fbe7d3;border-radius:2px"></div>
  <div class="a" style="left:38px;top:183px;font-size:3.6px;line-height:5.2px">Phone<br>1-888-ORVN-VIP (1-888-678-6847)<br><span class="muted">Mon–Fri: 9am–6pm EST</span></div>
  <div class="a" style="left:20px;top:213px;width:9px;height:9px;background:#fbe7d3;border-radius:2px"></div>
  <div class="a" style="left:38px;top:212px;font-size:3.6px;line-height:5.2px">Headquarters<br>OrvanoGoods<br>A Division of KRWZ Hospitality<br>[Address will be added]</div>
  <div class="a" style="left:20px;top:255px;width:168px;height:100px;background:var(--soft)"></div>
  <div class="a serif" style="left:28px;top:261px;font-size:6px">Our Concierge Services</div>
  <div class="a" style="left:28px;top:276px;font-size:3.4px;line-height:4.6px;display:flex;flex-direction:column;gap:4px">
    <div class="bullet"><span class="dot"></span><span><b class="serif">Personal Shopping</b><br><span class="muted">One-on-one assistance in selecting the perfect items</span></span></div>
    <div class="bullet"><span class="dot"></span><span><b class="serif">Custom Orders</b><br><span class="muted">Special requests and personalization services</span></span></div>
    <div class="bullet"><span class="dot"></span><span><b class="serif">Gift Consultation</b><br><span class="muted">Expert advice for luxury gifts and corporate gifting</span></span></div>
    <div class="bullet"><span class="dot"></span><span><b class="serif">B2B Partnership</b><br><span class="muted">Wholesale inquiries and partnership opportunities</span></span></div>
  </div>

  <div class="card" style="left:202px;top:135px;width:168px;height:255px"></div>
  <div class="a serif" style="left:211px;top:144px;font-size:8px">Send Us a Message</div>
  <div class="a or" style="left:218px;top:164px;font-size:3.6px">⚲ General Inquiry</div>
  <div class="a" style="left:275px;top:164px;font-size:3.6px">▣ B2B Inquiry</div>
  <div class="a" style="left:211px;top:172px;width:50px;border-top:0.7px solid var(--orange)"></div>
  <div class="a" style="left:211px;top:172px;width:150px;border-top:0.4px solid var(--line)"></div>
  <div class="field-label" style="left:211px;top:183px">First Name *</div><div class="field" style="left:211px;top:189px;width:72px"></div>
  <div class="field-label" style="left:289px;top:183px">Last Name *</div><div class="field" style="left:289px;top:189px;width:72px"></div>
  <div class="field-label" style="left:211px;top:212px">Email Address *</div><div class="field" style="left:211px;top:219px;width:150px">your@email.com</div>
  <div class="field-label" style="left:211px;top:241px">Phone Number</div><div class="field" style="left:211px;top:248px;width:150px">(555) 123-4567</div>
  <div class="field-label" style="left:211px;top:270px">Subject *</div><div class="field" style="left:211px;top:277px;width:150px"></div>
  <div class="field-label" style="left:211px;top:299px">Message *</div><div class="field" style="left:211px;top:306px;width:150px;height:48px">Tell us how we can assist you...</div>
  <div class="btn fill" style="left:211px;top:365px;width:150px;height:12px;line-height:12px">➤ Send Message</div>

  <div class="a" style="left:65px;top:425px;width:258px;height:45px;background:var(--soft)"></div>
  <div class="a serif center" style="top:429px;font-size:8px">Part of KRWZ Hospitality</div>
  <div class="a muted center" style="top:442px;font-size:3.6px;line-height:5.4px">OrvanoGoods is a proud division of KRWZ Hospitality, bringing the same commitment to excellence and<br>customer service to the luxury retail space.</div>
  <div class="a or center" style="top:462px;font-size:3.6px">Learn more about KRWZ Hospitality →</div>

  <footer class="foot">
    <div class="brand"><i></i>ORVANOGOODS</div>
    <div class="tag">A Division of KRWZ Hospitality<br>"Purveyors of Luxury Lifestyle Accoutrements."</div>
    <div class="col" style="left:110px"><b>Shop</b>All Collections<br>Cigar Accessories<br>Oils &amp; Fragrances<br>Attire &amp; Accessories</div>
    <div class="col" style="left:200px"><b>Business</b>Wholesale Portal<br>Partner Showcase<br>B2B Inquiries</div>
    <div class="col" style="left:290px"><b>Support</b>Contact &amp; Concierge<br>About Us<br>KRWZ Hospitality</div>
    <div class="rule"></div>
    <div class="copy">© 2026 OrvanoGoods. All rights reserved.</div>
  </footer>
</section>

<!-- ================= WHOLESALE PORTAL ================= -->
<section class="page" style="left:1439px;top:678px;width:390px;height:492px">
  <header class="nav">
    <div class="brand"><i></i>ORVANOGOODS</div>
    <div class="links"><span>Home</span><span>About</span><span>Retail Collections</span><span>Partner Showcase</span><span>Contact</span></div>
    <div class="nav-btn">Wholesale Portal</div>
    <div class="nav-ic"><svg width="5" height="5" viewBox="0 0 10 10"><circle cx="5" cy="3" r="2.2" fill="none" stroke="#fff"/><path d="M1 10a4 4 0 0 1 8 0" fill="none" stroke="#fff"/></svg><svg width="5" height="5" viewBox="0 0 10 10"><path d="M0 1h2l1.5 6h5L10 3H3" fill="none" stroke="#fff"/></svg></div>
  </header>
  <div class="dark-head" style="top:24px;height:96px"></div>
  <svg class="a" style="left:187px;top:43px" width="16" height="16" viewBox="0 0 16 16"><rect x="2" y="3" width="12" height="12" fill="none" stroke="#d96b0c" stroke-width="1.2"/><path d="M5 1v4M11 1v4M5 8h2M9 8h2M5 11h2M9 11h2" stroke="#d96b0c"/></svg>
  <div class="a serif w center" style="top:66px;font-size:13px">Wholesale Portal</div>
  <div class="a center" style="top:86px;font-size:4.6px;line-height:7px;color:#c9c9c9">Elevate your lounge. Impress your clientele. Partner with<br>OrvanoGoods.</div>

  <div class="a serif" style="left:38px;top:134px;font-size:8px">Partnership Benefits</div>
  <div class="a" style="left:38px;top:152px;width:150px;font-size:3.6px;line-height:5px;display:flex;flex-direction:column;gap:9px">
    <div class="bullet"><svg width="9" height="9" viewBox="0 0 9 9" style="flex:none"><circle cx="4.5" cy="4.5" r="4.5" fill="#fbe7d3"/><path d="M2.5 4.5l1.5 1.5 2.5-3" stroke="#d96b0c" fill="none" stroke-width=".8"/></svg><span style="margin-left:3px"><b class="serif" style="font-size:4.2px">Wholesale Pricing</b><br><span class="muted">Access exclusive pricing tiers based on order volume and partnership level.</span></span></div>
    <div class="bullet"><svg width="9" height="9" viewBox="0 0 9 9" style="flex:none"><circle cx="4.5" cy="4.5" r="4.5" fill="#fbe7d3"/><path d="M2.5 4.5l1.5 1.5 2.5-3" stroke="#d96b0c" fill="none" stroke-width=".8"/></svg><span style="margin-left:3px"><b class="serif" style="font-size:4.2px">Premium Product Selection</b><br><span class="muted">Curated collections specifically designed for lounges, venues, and special events.</span></span></div>
    <div class="bullet"><svg width="9" height="9" viewBox="0 0 9 9" style="flex:none"><circle cx="4.5" cy="4.5" r="4.5" fill="#fbe7d3"/><path d="M2.5 4.5l1.5 1.5 2.5-3" stroke="#d96b0c" fill="none" stroke-width=".8"/></svg><span style="margin-left:3px"><b class="serif" style="font-size:4.2px">Dedicated Account Manager</b><br><span class="muted">Personal support to help you select the perfect products for your clientele.</span></span></div>
    <div class="bullet"><svg width="9" height="9" viewBox="0 0 9 9" style="flex:none"><circle cx="4.5" cy="4.5" r="4.5" fill="#fbe7d3"/><path d="M2.5 4.5l1.5 1.5 2.5-3" stroke="#d96b0c" fill="none" stroke-width=".8"/></svg><span style="margin-left:3px"><b class="serif" style="font-size:4.2px">Partner Showcase</b><br><span class="muted">Featured placement on our Partner Showcase page to drive traffic to your venue.</span></span></div>
    <div class="bullet"><svg width="9" height="9" viewBox="0 0 9 9" style="flex:none"><circle cx="4.5" cy="4.5" r="4.5" fill="#fbe7d3"/><path d="M2.5 4.5l1.5 1.5 2.5-3" stroke="#d96b0c" fill="none" stroke-width=".8"/></svg><span style="margin-left:3px"><b class="serif" style="font-size:4.2px">Flexible Terms</b><br><span class="muted">Net payment terms and flexible ordering to support your business needs.</span></span></div>
  </div>
  <div class="a" style="left:38px;top:306px;width:150px;height:76px;background:var(--cream);border:0.5px solid #f1e3b8"></div>
  <div class="a serif or" style="left:46px;top:313px;font-size:5px">Who Can Apply?</div>
  <div class="a" style="left:46px;top:324px;font-size:3.6px;line-height:6.4px">
    • Licensed cigar lounges and smoking establishments<br>• Upscale bars and restaurants<br>• Private clubs and member organizations<br>• Special event planners and coordinators<br>• Luxury retailers and boutiques
  </div>

  <div class="card" style="left:202px;top:135px;width:150px;height:127px"></div>
  <div class="a or" style="left:222px;top:146px;font-size:3.8px">Login</div>
  <div class="a" style="left:246px;top:146px;font-size:3.8px">Apply for Account</div>
  <div class="a" style="left:211px;top:153px;width:30px;border-top:0.7px solid var(--orange)"></div>
  <div class="field-label" style="left:211px;top:167px">Email Address</div><div class="field" style="left:211px;top:174px;width:132px">✉ your@email.com</div>
  <div class="field-label" style="left:211px;top:196px">Password</div><div class="field" style="left:211px;top:203px;width:132px">🔒 ••••••••</div>
  <div class="a" style="left:211px;top:226px;font-size:3.4px">☐ Remember me</div>
  <div class="a or" style="left:308px;top:226px;font-size:3.4px">Forgot password?</div>
  <div class="btn fill" style="left:211px;top:239px;width:132px;height:12px;line-height:12px">Sign In</div>

  <footer class="foot">
    <div class="brand"><i></i>ORVANOGOODS</div>
    <div class="tag">A Division of KRWZ Hospitality<br>"Purveyors of Luxury Lifestyle Accoutrements."</div>
    <div class="col" style="left:110px"><b>Shop</b>All Collections<br>Cigar Accessories<br>Oils &amp; Fragrances<br>Attire &amp; Accessories</div>
    <div class="col" style="left:200px"><b>Business</b>Wholesale Portal<br>Partner Showcase<br>B2B Inquiries</div>
    <div class="col" style="left:290px"><b>Support</b>Contact &amp; Concierge<br>About Us<br>KRWZ Hospitality</div>
    <div class="rule"></div>
    <div class="copy">© 2026 OrvanoGoods. All rights reserved.</div>
  </footer>
</section>

<!-- ================= PRODUCT DETAIL ================= -->
<section class="page" style="left:557px;top:806px;width:390px;height:445px">
  <header class="nav">
    <div class="brand"><i></i>ORVANOGOODS</div>
    <div class="links"><span>Home</span><span>About</span><span>Retail Collections</span><span>Partner Showcase</span><span>Contact</span></div>
    <div class="nav-btn">Wholesale Portal</div>
    <div class="nav-ic"><svg width="5" height="5" viewBox="0 0 10 10"><circle cx="5" cy="3" r="2.2" fill="none" stroke="#fff"/><path d="M1 10a4 4 0 0 1 8 0" fill="none" stroke="#fff"/></svg><svg width="5" height="5" viewBox="0 0 10 10"><path d="M0 1h2l1.5 6h5L10 3H3" fill="none" stroke="#fff"/></svg></div>
  </header>
  <div class="a muted" style="left:20px;top:29px;font-size:3.4px">Home / Collections / <span style="color:var(--ink)">Premium Cedar Humidor</span></div>
  <div class="a" style="left:0;top:38px;width:390px;border-top:0.5px solid var(--line)"></div>
  <div class="a" style="left:20px;top:53px;font-size:3.8px">← Back to Collections</div>
  <div class="ph" role="img" aria-label="Cedar humidor with round hygrometer" style="left:20px;top:68px;width:168px;height:169px;background:linear-gradient(160deg,#f0f0f0,#cfcfcf)"></div>
  <div class="tag-badge" style="left:26px;top:74px">Limited Edition</div>
  <div class="ph" role="img" aria-label="Humidor thumbnail, selected" style="left:20px;top:241px;width:39px;height:39px;background:linear-gradient(160deg,#e8e8e8,#c7c7c7);outline:0.8px solid var(--orange)"></div>
  <div class="ph" role="img" aria-label="Humidor thumbnail, alternate view" style="left:63px;top:241px;width:39px;height:39px;background:linear-gradient(160deg,#e8e8e8,#c7c7c7)"></div>

  <div class="a muted" style="left:202px;top:69px;font-size:3.4px">Cigar Accessories</div>
  <div class="a serif" style="left:202px;top:76px;font-size:10px">Premium Cedar Humidor</div>
  <div class="a" style="left:202px;top:92px;font-size:4px"><span class="or">★★★★</span><span style="color:#ccc">★</span> <span class="muted" style="font-size:3.2px">4.9 (37 reviews)</span></div>
  <div class="a or" style="left:202px;top:102px;font-size:9px">$899</div>
  <div class="a muted" style="left:202px;top:120px;width:160px;font-size:3.8px;line-height:5.6px">Hand-crafted Spanish cedar humidor with precision hygrometer. This exceptional piece is designed to maintain the perfect environment for your cigar collection.</div>
  <div class="a" style="left:202px;top:150px;font-size:3.6px">Features</div>
  <div class="a" style="left:202px;top:159px;font-size:3.8px;line-height:7px"><span class="or">✓</span> Spanish cedar lining<br><span class="or">✓</span> Digital hygrometer and thermometer<br><span class="or">✓</span> Holds up to 100 cigars<br><span class="or">✓</span> Handmade construction<br><span class="or">✓</span> Lifetime warranty</div>
  <div class="a muted" style="left:202px;top:227px;font-size:3.4px">Quantity:</div>
  <div class="a" style="left:227px;top:224px;width:36px;height:9px;border:0.5px solid var(--line);font-size:3.6px;display:flex;justify-content:space-around;align-items:center"><span>-</span><span>1</span><span>+</span></div>
  <div class="btn fill" style="left:202px;top:243px;width:142px;height:15px;line-height:15px">🛒 Add to Cart</div>
  <div class="a" style="left:350px;top:243px;width:20px;height:15px;border:0.5px solid var(--line);font-size:5px;text-align:center;line-height:15px">♡</div>
  <div class="a" style="left:202px;top:266px;font-size:3.4px;color:#2e9a4a">✓ In stock and ready to ship</div>
  <div class="a" style="left:202px;top:280px;width:168px;height:56px;background:var(--soft)"></div>
  <div class="a serif" style="left:209px;top:285px;font-size:4.2px">Why Choose OrvanoGoods?</div>
  <div class="a muted" style="left:209px;top:295px;font-size:3.4px;line-height:6px"><span class="or">✓</span> Authenticity guaranteed on all products<br><span class="or">✓</span> White-glove delivery service available<br><span class="or">✓</span> Concierge support for all purchases<br><span class="or">✓</span> 30-day satisfaction guarantee</div>

  <footer class="foot">
    <div class="brand"><i></i>ORVANOGOODS</div>
    <div class="tag">A Division of KRWZ Hospitality<br>"Purveyors of Luxury Lifestyle Accoutrements."</div>
    <div class="col" style="left:110px"><b>Shop</b>All Collections<br>Cigar Accessories<br>Oils &amp; Fragrances<br>Attire &amp; Accessories</div>
    <div class="col" style="left:200px"><b>Business</b>Wholesale Portal<br>Partner Showcase<br>B2B Inquiries</div>
    <div class="col" style="left:290px"><b>Support</b>Contact &amp; Concierge<br>About Us<br>KRWZ Hospitality</div>
    <div class="rule"></div>
    <div class="copy">© 2026 OrvanoGoods. All rights reserved.</div>
  </footer>
</section>

<!-- ================= ABOUT ================= -->
<section class="page" style="left:115px;top:895px;width:389px;height:960px">
  <header class="nav">
    <div class="brand"><i></i>ORVANOGOODS</div>
    <div class="links"><span>Home</span><span class="on">About</span><span>Retail Collections</span><span>Partner Showcase</span><span>Contact</span></div>
    <div class="nav-btn">Wholesale Portal</div>
    <div class="nav-ic"><svg width="5" height="5" viewBox="0 0 10 10"><circle cx="5" cy="3" r="2.2" fill="none" stroke="#fff"/><path d="M1 10a4 4 0 0 1 8 0" fill="none" stroke="#fff"/></svg><svg width="5" height="5" viewBox="0 0 10 10"><path d="M0 1h2l1.5 6h5L10 3H3" fill="none" stroke="#fff"/></svg></div>
  </header>
  <div class="ph" role="img" aria-label="Dark lounge interior with leather seating" style="left:0;top:24px;width:389px;height:99px;background:linear-gradient(90deg,#2a2a2c,#1a1b1e 50%,#2c2c2e)"></div>
  <svg class="a" style="left:187px;top:47px" width="16" height="13" viewBox="0 0 16 13"><path d="M1 3l3.5 4L8 1l3.5 6L15 3l-1.5 8h-11z" fill="none" stroke="#d96b0c" stroke-width="1.2"/></svg>
  <div class="a serif w center" style="top:70px;font-size:13px">About OrvanoGoods</div>
  <div class="a center" style="top:92px;font-size:4.6px;color:#ddd">A Division of KRWZ Hospitality</div>

  <div class="h-sec center" style="top:146px">Our Mission</div>
  <div class="a muted center" style="top:165px;font-size:4.8px;line-height:8px">OrvanoGoods exists to bridge the gap between exceptional luxury goods and those<br>who truly appreciate them—whether you're an individual connoisseur seeking the<br>extraordinary or a business owner curating unforgettable experiences for your clientele.</div>
  <div class="a muted" style="left:75px;top:206px;width:240px;font-size:3.8px;line-height:5.6px">We are purveyors in the truest sense: seekers, curators, and providers of luxury lifestyle accoutrements that embody craftsmanship, exclusivity, and timeless elegance. From premium cigar accessories to refined oils and fragrances, from distinguished attire to one-of-a-kind collectibles, every item in our collection is selected with discerning taste.</div>

  <div class="a" style="left:10px;top:262px;width:369px;height:175px;background:var(--soft)"></div>
  <div class="h-sec center" style="top:281px">Serving Two Worlds</div>
  <div class="card" style="left:20px;top:306px;width:167px;height:119px"></div>
  <svg class="a" style="left:29px;top:316px" width="12" height="12" viewBox="0 0 12 12"><circle cx="6" cy="6" r="5" fill="none" stroke="#d96b0c"/><circle cx="6" cy="6" r="2.5" fill="none" stroke="#d96b0c"/></svg>
  <div class="a serif" style="left:29px;top:334px;font-size:6px">For Discerning Consumers</div>
  <div class="a small" style="left:29px;top:346px;width:150px">We cater to individuals who demand more than mass-market luxury. Our retail collections offer:</div>
  <div class="a" style="left:29px;top:365px;font-size:3.6px;line-height:6.3px"><span class="or">•</span> Exclusive, limited-edition items<br><span class="or">•</span> Focus on craftsmanship and quality<br><span class="or">•</span> One-of-a-kind luxury pieces<br><span class="or">•</span> Personal indulgence and self-expression<br><span class="or">•</span> Concierge service for custom orders</div>
  <div class="card" style="left:201px;top:306px;width:169px;height:119px;background:var(--black)"></div>
  <svg class="a" style="left:210px;top:316px" width="12" height="12" viewBox="0 0 12 12"><circle cx="4" cy="4" r="2" fill="none" stroke="#d96b0c"/><circle cx="8.5" cy="4.5" r="1.6" fill="none" stroke="#d96b0c"/><path d="M0.5 11a3.5 3.5 0 0 1 7 0M7 10.5a3 3 0 0 1 4.5-2" fill="none" stroke="#d96b0c"/></svg>
  <div class="a serif w" style="left:210px;top:334px;font-size:6px">For Sophisticated Businesses</div>
  <div class="a small" style="left:210px;top:346px;width:152px;color:#bbb">We partner with lounges, licensed establishments, and special event organizers who want to elevate their offerings:</div>
  <div class="a w" style="left:210px;top:365px;font-size:3.6px;line-height:6.3px"><span class="or">•</span> Wholesale pricing for approved partners<br><span class="or">•</span> Product quality that enhances brand elevation<br><span class="or">•</span> Curated selections for your clientele<br><span class="or">•</span> Partnership opportunities and support<br><span class="or">•</span> Dedicated B2B account management</div>

  <svg class="a" style="left:188px;top:472px" width="13" height="16" viewBox="0 0 13 16"><circle cx="6.5" cy="5.5" r="4.5" fill="none" stroke="#d96b0c" stroke-width="1.2"/><path d="M3.5 9l-1 6 4-2 4 2-1-6" fill="none" stroke="#d96b0c" stroke-width="1.2"/></svg>
  <div class="h-sec center" style="top:495px">Part of the KRWZ Family</div>
  <div class="a muted" style="left:75px;top:520px;width:240px;font-size:3.8px;line-height:5.6px">OrvanoGoods is a proud division of KRWZ Hospitality, a company rooted in creating exceptional experiences in the hospitality industry. Drawing on KRWZ's expertise in serving discerning guests and creating memorable moments, OrvanoGoods extends that same commitment to excellence into the world of luxury retail and wholesale.<br>Our connection to KRWZ Hospitality gives us unique insight into what lounges, venues, and businesses need to impress their most sophisticated patrons—while also understanding what individual consumers seek when investing in luxury items.</div>
  <div class="a or center" style="top:580px;font-size:3.8px">Visit KRWZHospitality.com →</div>

  <div class="band-orange" style="top:609px;height:128px"></div>
  <div class="a serif w center" style="top:630px;font-size:10px">Our Philosophy</div>
  <div class="a w center serif" style="top:656px;font-size:5px;line-height:15px;font-style:italic;font-family:'Inter',sans-serif">"Curated for connoisseurs. Crafted for lounges."<br>"From the humidor to the wardrobe—OrvanoGoods delivers indulgence."<br>"Elevate your lounge. Impress your clientele."<br>"Curating limited edition luxury items is fun... but one of a kind is LUXE."</div>

  <div class="h-sec center" style="top:760px">What We Stand For</div>
  <div class="a" style="left:68px;top:786px;width:13px;height:13px;border-radius:50%;background:#fbe7d3"></div>
  <div class="a" style="left:188px;top:786px;width:13px;height:13px;border-radius:50%;background:#fbe7d3"></div>
  <div class="a" style="left:308px;top:786px;width:13px;height:13px;border-radius:50%;background:#fbe7d3"></div>
  <div class="a serif" style="left:24px;top:808px;width:101px;text-align:center;font-size:6px">Exclusivity</div>
  <div class="a serif" style="left:144px;top:808px;width:101px;text-align:center;font-size:6px">Craftsmanship</div>
  <div class="a serif" style="left:260px;top:808px;width:109px;text-align:center;font-size:6px">Partnership</div>
  <div class="a small" style="left:20px;top:820px;width:109px;text-align:center">We seek out items that are rare, limited, and exceptional—never mass-produced mediocrity.</div>
  <div class="a small" style="left:140px;top:820px;width:109px;text-align:center">Every product represents the pinnacle of quality and artisanal skill.</div>
  <div class="a small" style="left:258px;top:820px;width:113px;text-align:center">We build lasting relationships with our customers and business partners based on trust and mutual success.</div>

  <footer class="foot">
    <div class="brand"><i></i>ORVANOGOODS</div>
    <div class="tag">A Division of KRWZ Hospitality<br>"Purveyors of Luxury Lifestyle Accoutrements."</div>
    <div class="col" style="left:110px"><b>Shop</b>All Collections<br>Cigar Accessories<br>Oils &amp; Fragrances<br>Attire &amp; Accessories</div>
    <div class="col" style="left:200px"><b>Business</b>Wholesale Portal<br>Partner Showcase<br>B2B Inquiries</div>
    <div class="col" style="left:290px"><b>Support</b>Contact &amp; Concierge<br>About Us<br>KRWZ Hospitality</div>
    <div class="rule"></div>
    <div class="copy">© 2026 OrvanoGoods. All rights reserved.</div>
  </footer>
</section>

</div>
</body>
</html>
```